PillPeak website blog. Simple medical advice given in clear yes or no answers that save people money

I am developing a new web page that provides medical care cost savings at the consumers' fingertips. I need a web page that is clean, concise, and attractive for me to put my valuable medical information on. The information I provide is simple to obtain, yet very valuable to the consumer, and answered in a yes or no format. For example, A person may wonder if they need an antibiotic for cold like symptoms. Seeing a doctor for an antibiotic is very expensive. But with simple and clear advice at their fingertips, they can confidently avoid having to pay $200 or more to see a doctor and get an antibiotic. This is kind of like consumer reports for medical services.

Target Market(s)

People who are savvy shoppers and want to save money on healthcare. Likely younger ages between 21 and 60, who are mobile, readily use iphones, and want strong evidence based research to guide their decisions.

Industry/Entity Type

Coding

Number of Pages Required

Colors

Requirements
Must have
• A template on the "Question" and "Answer" page that can be edited many times that can be edited many times. The Confidence rating scale would need to be edited as well. The "Date Researched" the "PillPeak Pilluminate" and "References" all need to be able to be edited. This website must be very clear and simple to understand. A medical question is posed with a yes or no answer, then answered and given a confidence rating, we then tell them how much money they saved by going to our website.
Nice to have
• We want this to be slightly fun, vibrant, warm and inviting. This will be sometime later converted into an app format. Quirky, some humor to keep it interesting.
Should not have
• No sterile looking medical images. Not boring.

```html
<!DOCTYPE html>
<html lang="en">
<head>
<meta charset="utf-8">
<title>PillPeak</title>
<link rel="stylesheet" href="https://fonts.googleapis.com/css2?family=Montserrat:wght@500;600;700&family=Open+Sans:ital,wght@0,400;0,700;1,400&display=swap">
<style>
:root{
  --ink:#222;
  --brand-blue:#1c5fae;
  --brand-red:#e3071d;
  --hero-deep:#0b3f78;
  --hero-mid:#15589a;
  --hero-light:#3f86c6;
  --white:#fff;
  --line:#c9c9c9;
  --footer:#141414;
}
*{margin:0;padding:0;box-sizing:border-box}
html,body{width:884px;height:1200px;overflow:hidden;background:var(--white);font-family:"Open Sans",sans-serif;color:var(--ink)}
.page{position:relative;width:884px;height:1200px}
.header{position:absolute;left:0;top:0;width:884px;height:103px;border-bottom:1px solid var(--line)}
.brand{position:absolute;left:80px;top:30px;display:flex;align-items:center;gap:8px}
.brand-dot{width:30px;height:30px;border-radius:50%;background:var(--brand-blue)}
.brand-name{font-family:"Montserrat",sans-serif;font-weight:700;font-size:26px;color:var(--brand-blue)}
.tagline{position:absolute;left:262px;top:25px;font-family:"Montserrat",sans-serif;font-weight:600;font-size:17.5px;line-height:27px;color:var(--ink)}
.search{position:absolute;left:573px;top:42px;width:229px;height:27px;border-bottom:1px solid #999;display:flex;justify-content:space-between;align-items:center;font-size:12.5px;color:#666}
.nav{position:absolute;left:0;top:103px;width:884px;height:34px;display:flex;justify-content:center;gap:20px;align-items:center;font-family:"Montserrat",sans-serif;font-weight:500;font-size:11.5px;color:var(--ink)}
.hero{position:absolute;left:0;top:137px;width:884px;height:421px;background:linear-gradient(120deg,var(--hero-deep) 0%,var(--hero-mid) 55%,var(--hero-light) 100%)}
.hero-art{position:absolute;right:0;top:0;width:290px;height:421px;background:radial-gradient(circle at 60% 45%,rgba(140,190,235,.45),rgba(20,88,154,0) 70%)}
.side-menu{position:absolute;left:82px;top:55px;display:flex;flex-direction:column;gap:6px}
.side-menu a{display:flex;width:187px;height:38px;border:2px solid var(--white);align-items:center;justify-content:center;color:var(--white);font-weight:700;font-size:11.5px;text-decoration:none;text-transform:uppercase}
.headline{position:absolute;left:319px;top:136px;font-family:"Montserrat",sans-serif;font-weight:700;font-size:32.5px;line-height:44px;color:var(--white)}
.subline{position:absolute;left:324px;top:278px;font-family:"Montserrat",sans-serif;font-weight:600;font-size:19px;color:var(--white)}
.dots{position:absolute;left:424px;top:352px;display:flex;gap:3px}
.dots span{width:10px;height:10px;border-radius:50%;border:1.5px solid var(--white)}
.dots span.on{background:var(--white)}
.signup{position:absolute;left:0;top:622px;width:884px;text-align:center}
.signup h2{font-family:"Montserrat",sans-serif;font-weight:700;font-size:29px;color:var(--ink)}
.email{position:absolute;left:169px;top:687px;width:546px;height:44px;border:1px solid #999;display:flex;align-items:center;padding-left:21px;gap:8px;font-size:12.5px;color:#444}
.ask{position:absolute;left:0;top:762px;width:884px;text-align:center;font-family:"Montserrat",sans-serif;font-weight:500;font-size:20px}
.cta{position:absolute;left:315px;top:817px;width:254px;height:45px;border-radius:23px;background:var(--brand-red);color:var(--white);display:flex;align-items:center;justify-content:center;font-weight:700;font-size:12.5px}
.footer{position:absolute;left:0;top:936px;width:884px;height:264px;background:var(--footer);color:var(--white);text-align:center}
.social{position:absolute;left:360px;top:53px;display:flex;gap:6px}
.social span{width:37px;height:37px;border-radius:50%;border:1.5px solid var(--white)}
.links{position:absolute;left:0;top:107px;width:884px;font-size:11px}
.copy{position:absolute;left:0;top:136px;width:884px;font-size:11px}
.fine{position:absolute;left:155px;top:172px;width:574px;font-size:9px;font-style:italic;line-height:17px}
</style>
</head>
<body>
<div class="page">
  <header class="header">
    <div class="brand"><span class="brand-dot"></span><span class="brand-name">PillPeak</span></div>
    <div class="tagline">CLEAR VALUABLE<br>HEALTH ADVICE RIGHT NOW</div>
    <div class="search"><span>Search</span>
      <svg width="13" height="13" viewBox="0 0 13 13"><circle cx="5.5" cy="5.5" r="4" fill="none" stroke="#555" stroke-width="2"/><line x1="8.5" y1="8.5" x2="12" y2="12" stroke="#555" stroke-width="2"/></svg>
    </div>
  </header>
  <nav class="nav"><span>PREV/SCREENING</span><span>WOMEN'S HEALTH</span><span>MEN'S HEALTH</span><span>MEDS</span><span>SURGERY</span><span>IMAGERY</span><span>PEDS</span><span>CONTACT US</span></nav>
  <section class="hero">
    <div class="hero-art" role="img" aria-label="Cluster of circular medical icons on a blue hexagon network background"></div>
    <div class="side-menu">
      <a>Who we are ?</a><a>How it works</a><a>How we know</a><a>Evidence based research</a><a>Dr.Marlow</a><a>Who we are not</a><a>Are we biased?</a>
    </div>
    <div class="headline">DON'T SPEND<br>ANOTHER CLINIC ON<br>YOUR HEALTH BEFORE</div>
    <div class="subline">CHECKING US OUT ! IT'S FREE</div>
    <div class="dots"><span class="on"></span><span></span><span></span></div>
  </section>
  <section class="signup"><h2>BECOME A&nbsp; PILLPEAK TODAY!</h2></section>
  <div class="email">
    <svg width="12" height="9" viewBox="0 0 12 9"><rect width="12" height="9" fill="#555"/><path d="M0 0 L6 5 L12 0" fill="none" stroke="#fff" stroke-width="1"/></svg>
    <span>Enter Email Address</span>
  </div>
  <div class="ask">Ask a Question Here!</div>
  <div class="cta">IF IT IS WORTHY, WELL POST IT!</div>
  <footer class="footer">
    <div class="social" aria-label="Social links"><span></span><span></span><span></span><span></span></div>
    <div class="links">Help &nbsp;|&nbsp;&nbsp; FAQ &nbsp;|&nbsp;&nbsp; Support &nbsp;|&nbsp;&nbsp; Sitemap &nbsp;|&nbsp;&nbsp; Terms Of Use &nbsp;|&nbsp;&nbsp; Privacy Statement</div>
    <div class="copy">Copyrights © 2018, PillPeak. All rights reserved.</div>
    <p class="fine">Nemo enim ipsam voluptatem quia voluptas sit aspernatur aut odit aut fugit, sed quia consequuntur magni dolores eos qui ratione voluptatem sequi nesciunt. Neque porro quisquam est, qui dolorem ipsum quia dolor sit amet, consectetur, adipisci velit, sed quia non numquam quis nostrum exercitationem ullam corporis suscipit laboriosam, nisi ut aliquid ex ea commodi consequatu</p>
  </footer>
</div>
</body>
</html>
```